Flyer for Dessert Cafe event launch

Hi
We are launching a new initiative at our cafe - this is the plan:
- We will open Saturday nights to serve desserts, tea and coffee and other after dinner deliciousness (no alcohol)
- Customers stop in and enjoy something sweets on the way home from dinner or movies. We'd decorate the garden with fairy lights, candles and lanterns and create a beautiful and relaxing (and romantic) after dinner atmosphere - maybe a little acoustic guitar
- For the menu we are thinking everything from chocolate mousse and cheesecake to tiramisu and dessert mocktails and even sorbet and gelato.
- The dessert cafe would probably trade from 7pm till 11pm.
Please check out www.brelvantable.com for our current branding feel.

We need an A4 flyer designed to promote this new venture.
I want the design to incorporate trees with fairy lights in them - and hearts - as we will be launching on Valentines Day evening (and the heart is part of our branding). Obviously the design needs to be tied in with our current branding - logo attached in various forms I am happy for you to use whichever fits best with your design. I have also attached some images that inspire me for this project - but they don't need to be used.

The following information will need to be included:

On the way home from dinner, or just craving something sweet?
Join us for Dessert!
Unwind - Relax - Indulge
7pm - 11pm every Saturday night
Starting on Valentines Day
All desserts handmade in-house - with love! *** Coffee *** Tea *** Mocktails *** Share platters available ***Gluten Free, Dairy Free and Vegan options *** Take-Away Available
Live Music

2847 Ridgeway Drive, Harlow Flats (five minutes from Kestrel Bay)
(03) 5391 8264
www.brelvantable.com
Please include the Facebook - Twiiter and Instagram Icons

```html
<!DOCTYPE html>
<html lang="en">
<head>
<meta charset="utf-8">
<title>Brelvan Table – Saturday Night Dessert</title>
<link href="https://fonts.googleapis.com/css2?family=Didact+Gothic&family=Handlee&display=swap" rel="stylesheet">
<style>
  :root {
    --night-top: #1c1f4a;
    --night-mid: #3a3f7a;
    --dusk-blue: #5a7396;
    --floor-grey: #7f93aa;
    --lantern-orange: #e8501c;
    --band-orange: #e0561d;
    --panel-orange: #d9561f;
    --heart-pink: #f3c1b0;
    --ornament-tint: rgba(255,255,255,0.14);
    --white: #ffffff;
    --rule: rgba(255,255,255,0.75);
  }
  * { margin: 0; padding: 0; box-sizing: border-box; }
  html, body { width: 848px; height: 1200px; overflow: hidden; background: #222; }
  .flyer {
    position: relative; width: 848px; height: 1200px; overflow: hidden;
    font-family: "Didact Gothic", "Century Gothic", sans-serif; color: var(--white);
  }
  .scene-photo {
    position: absolute; inset: 0;
    background:
      radial-gradient(ellipse 170px 230px at 250px 860px, rgba(255,140,60,0.85), rgba(232,80,28,0.35) 55%, transparent 80%),
      radial-gradient(ellipse 260px 320px at 240px 760px, rgba(200,90,130,0.55), transparent 75%),
      radial-gradient(ellipse 300px 200px at 180px 330px, rgba(240,140,60,0.45), transparent 70%),
      radial-gradient(ellipse 360px 260px at 680px 250px, rgba(120,150,220,0.45), transparent 70%),
      linear-gradient(180deg, var(--night-top) 0%, var(--night-mid) 35%, var(--dusk-blue) 70%, var(--floor-grey) 100%);
  }
  .brand {
    position: absolute; left: -20px; top: -40px; width: 290px; height: 290px;
    border: 2px solid var(--white); border-radius: 50%;
    display: flex; align-items: center; justify-content: center;
  }
  .brand-name { font-size: 34px; color: var(--white); padding-left: 20px; font-weight: 400; }
  .headline {
    position: absolute; left: 385px; top: 33px; width: 370px;
    text-align: center; font-size: 40px; line-height: 45px; font-weight: 400;
    text-shadow: 0 0 4px rgba(0,0,0,0.4);
  }
  .band { position: absolute; left: 0; top: 190px; width: 848px; height: 190px; }
  .band-title {
    position: absolute; left: 0; width: 848px; top: 270px;
    text-align: center; font-family: "Handlee", cursive; font-size: 62px; font-weight: 400;
  }
  .launch {
    position: absolute; left: 35px; top: 474px; width: 390px; text-align: center;
    font-family: "Handlee", cursive; font-size: 58px; line-height: 72px; color: var(--lantern-orange);
    text-shadow: 0 0 6px #fff, 0 0 10px #fff;
  }
  .ornament { position: absolute; left: 470px; width: 340px; height: 80px; background: var(--ornament-tint); border-radius: 40px; }
  .ornament.top { top: 385px; }
  .ornament.bottom { top: 960px; }
  .offer-panel {
    position: absolute; left: 508px; top: 465px; width: 262px; height: 490px;
    background: var(--panel-orange); text-align: center;
  }
  .offer-lead { font-family: "Handlee", cursive; line-height: 1; margin-top: 28px; }
  .offer-lead .l1 { font-size: 38px; display: block; }
  .offer-lead .l2 { font-size: 44px; display: block; margin-top: 8px; }
  .offer-lead .l3 { font-size: 20px; display: block; margin-top: 10px; }
  .offer-list { list-style: none; margin-top: 30px; font-size: 20px; line-height: 25px; }
  .offer-list li { padding: 7px 4px; }
  .offer-list li + li { border-top: 1px solid var(--rule); }
  .offer-list li:last-child { border-top: none; }
  .heart { font-size: 15px; color: var(--heart-pink); margin: 0 2px; }
  .hours { position: absolute; left: 25px; top: 1058px; font-size: 35px; }
  .contact { position: absolute; left: 82px; top: 1105px; font-size: 18px; line-height: 28px; font-style: normal; }
  .contact .web { font-size: 25px; }
  .social { position: absolute; left: 525px; top: 1110px; display: flex; gap: 14px; list-style: none; }
  .social li { width: 70px; height: 70px; background: var(--white); border-radius: 6px; }
</style>
</head>
<body>
<main class="flyer">
  <div class="scene-photo" role="img" aria-label="Night garden with blurred fairy lights and a red lantern with a glowing heart cut-out on a wooden deck"></div>

  <div class="brand"><span class="brand-name">Brelvan Table</span></div>

  <h2 class="headline">On the way<br>home from dinner,<br>or just craving<br>something sweet?</h2>

  <svg class="band" viewBox="0 190 848 190" aria-hidden="true">
    <path d="M0,240 Q430,290 848,205 L848,300 Q430,385 0,352 Z" fill="var(--band-orange)"/>
    <path d="M0,236 Q430,286 848,201" fill="none" stroke="var(--white)" stroke-width="2"/>
  </svg>
  <h1 class="band-title">Join us for Dessert !</h1>

  <p class="launch">Starting on<br>Valentines Day</p>

  <div class="ornament top" role="img" aria-label="Decorative lace scroll"></div>
  <section class="offer-panel">
    <p class="offer-lead"><span class="l1">All desserts</span><span class="l2">handmade</span><span class="l3">in-house with love!</span></p>
    <ul class="offer-list">
      <li>Coffee<span class="heart">♥</span>Tea<span class="heart">♥</span>Mocktails</li>
      <li>Share platters available</li>
      <li>Gluten Free<span class="heart">♥</span>Dairy Free<br>and Vegan options</li>
      <li>Take-Away Available</li>
      <li>Unwind<span class="heart">♥</span>Relax<span class="heart">♥</span>Indulge</li>
      <li>Live Music</li>
    </ul>
  </section>
  <div class="ornament bottom" role="img" aria-label="Decorative lace scroll"></div>

  <p class="hours">7pm - 11pm every Saturday night</p>
  <address class="contact">
    2847 Ridgeway Drive, Harlow Flats<br>
    (five minutes from Kestrel Bay)<br>
    (03) 5391 8264 • <span class="web">www.brelvantable.com</span>
  </address>
  <ul class="social" aria-label="Social media">
    <li></li><li></li><li></li>
  </ul>
</main>
</body>
</html>
```